Vantro cards

I am in the auto motive, transportation business I would like a business card that is Something cool, modern edgy, having to do with car culture. I offer towing service for high and exotic cars. I also provide towing for collisions and car accidents. I offer open and enclosed transport nationwide.

Target Market(s)

Car culture people high end auto collectors

Industry/Entity Type

Towing car carrier

Contact Information for Business Card

My company colors black yellow and silver

Font styles to use
Serif

```html
<!DOCTYPE html>
<html lang="en">
<head>
<meta charset="utf-8">
<title>Vantro Transportation business cards</title>
<link href="https://fonts.googleapis.com/css2?family=Montserrat:wght@400;600;800&display=swap" rel="stylesheet">
<style>
  :root {
    --backdrop: #e6e3dd;
    --ink: #050505;
    --yellow: #f7dc54;
    --silver-light: #f6f6f6;
    --silver-mid: #c4c4c4;
    --silver-dark: #8a8a8a;
    --text-light: #f2f2f2;
    --text-muted: #d0d0d0;
  }
  * { margin: 0; padding: 0; box-sizing: border-box; }
  html, body { width: 900px; height: 1200px; overflow: hidden; }
  body {
    background: var(--backdrop);
    font-family: "Montserrat", Arial, sans-serif;
    position: relative;
  }
  .card {
    position: absolute;
    left: 80px;
    width: 742px;
    height: 440px;
    border-radius: 30px;
    overflow: hidden;
    box-shadow: 0 6px 18px rgba(0,0,0,0.35);
  }
  .silver {
    background:
      conic-gradient(from 200deg at 50% 45%,
        var(--silver-light), var(--silver-mid), var(--silver-light),
        var(--silver-dark), var(--silver-light), var(--silver-mid),
        var(--silver-light), var(--silver-dark), var(--silver-light));
  }
  /* front */
  .card-front { top: 132px; }
  .front-brand {
    position: absolute; left: 0; top: 0; width: 371px; height: 100%;
    display: flex; align-items: center; justify-content: center;
  }
  .front-info {
    position: absolute; left: 371px; top: 0; right: 0; height: 100%;
    background: var(--ink); color: var(--text-light);
  }
  .accent-tab {
    position: absolute; left: 371px; top: 186px; width: 7px; height: 72px;
    background: var(--yellow); border-radius: 0 4px 4px 0;
  }
  .brand-name {
    font-weight: 800; color: var(--ink); text-align: center;
    text-transform: uppercase; line-height: 1.05;
    display: flex; align-items: center; gap: 12px;
  }
  .brand-mark { width: 22px; height: 22px; background: var(--yellow); flex: none; }
  .brand-name span { display: block; }
  .front-brand .brand-name { font-size: 30px; }
  .person-name {
    position: absolute; left: 36px; top: 106px;
    font-size: 26px; font-weight: 600; color: var(--yellow);
  }
  .person-role { position: absolute; left: 36px; top: 139px; font-size: 16px; color: var(--text-muted); }
  .contact-list { position: absolute; left: 36px; top: 186px; list-style: none; font-size: 16px; }
  .contact-list li { display: flex; align-items: center; gap: 10px; height: 21.5px; }
  .contact-list svg { width: 15px; height: 13px; fill: var(--yellow); flex: none; }
  .address { position: absolute; left: 37px; top: 272px; font-size: 16px; line-height: 20px; font-style: normal; }
  /* back */
  .card-back { top: 638px; }
  .back-brand {
    position: absolute; left: 0; right: 0; top: 0; height: 360px;
    display: flex; align-items: center; justify-content: center;
  }
  .back-brand .brand-name { font-size: 36px; }
  .back-rule { position: absolute; left: 0; right: 0; top: 364px; height: 5px; background: var(--yellow); }
  .back-band {
    position: absolute; left: 0; right: 0; top: 382px; bottom: 0;
    background: var(--ink); color: var(--text-muted);
    display: flex; align-items: center; justify-content: center;
    font-size: 16px; letter-spacing: 0.3px;
  }
</style>
</head>
<body>
  <section class="card card-front">
    <div class="front-brand silver">
      <div class="brand-name"><i class="brand-mark"></i><div><span>Vantro</span><span>Transportation</span></div></div>
    </div>
    <div class="front-info">
      <h1 class="person-name">Dana Reyes</h1>
      <p class="person-role">Owner</p>
      <ul class="contact-list">
        <li><svg viewBox="0 0 16 14" aria-hidden="true"><path d="M1 4c0-2 2-3 7-3s7 1 7 3v1h-3V4H4v1H1zM4 6h8l2 7H2z"/></svg>(555) 014-2290</li>
        <li><svg viewBox="0 0 16 14" aria-hidden="true"><path d="M1 2h14v1L8 8 1 3zM1 5l7 5 7-5v7H1z"/></svg>info@vantrotransportation.com</li>
        <li><svg viewBox="0 0 16 14" aria-hidden="true"><circle cx="8" cy="7" r="6.5"/></svg>www.vantrotransportation.com</li>
      </ul>
      <address class="address">48 Ridge Road<br>Millbrook, PA 17010</address>
    </div>
    <div class="accent-tab"></div>
  </section>

  <section class="card card-back silver">
    <div class="back-brand">
      <div class="brand-name"><i class="brand-mark"></i><div><span>Vantro</span><span>Transportation</span></div></div>
    </div>
    <div class="back-rule"></div>
    <div class="back-band">www.vantrotransportation</div>
  </section>
</body>
</html>
```